Business Card & Letterhead Design

We a financial advice company based in Australia. We provide advice to wealthy farmers.

We are changing our business name FROM Brightvale Financial TO Tallowmere Wealth and we need a new letterhead and double sided business card design

Attached is designs from our previous branding (Brightvale Financial) as it includes all the details we require on the new Tallowmere Wealth business cards and letterhead.

Need extra days to review

```html
<!DOCTYPE html>
<html lang="en">
<head>
<meta charset="utf-8">
<title>Tallowmere Wealth – Business Card</title>
<link href="https://fonts.googleapis.com/css2?family=Cinzel:wght@400;500&family=Montserrat:wght@300;400;500&display=swap" rel="stylesheet">
<style>
  :root{
    --page:#e9eaeb;
    --slate:#5e6a6f;
    --charcoal:#4a4d50;
    --mid-grey:#8d9194;
    --paper:#ffffff;
    --ink:#3f4346;
    --accent-ink:#6c7478;
    --light:#f4f5f5;
  }
  *{margin:0;padding:0;box-sizing:border-box}
  html,body{width:1200px;height:900px;overflow:hidden;background:var(--page)}
  .canvas{position:relative;width:1200px;height:900px}
  .card{position:absolute;left:300px;width:600px;height:365px;border-radius:22px;overflow:hidden;box-shadow:0 6px 18px rgba(0,0,0,.15)}
  .card--front{top:60px;background:var(--slate);color:var(--light)}
  .card--back{top:475px;background:var(--paper);color:var(--ink)}

  /* front */
  .front__brand{position:absolute;left:48px;top:92px;font-family:"Cinzel",serif;font-size:25px;letter-spacing:1px;color:var(--light)}
  .services{position:absolute;left:48px;top:142px;list-style:none}
  .services li{display:flex;align-items:center;gap:12px;font-family:"Cinzel",serif;font-size:16px;letter-spacing:.5px;line-height:27px}
  .services li::before{content:"";width:12px;height:12px;border:1.5px solid var(--light);border-radius:50%}
  .licensee{position:absolute;left:48px;top:262px;font-family:"Montserrat",sans-serif;font-weight:300;font-size:13.5px;line-height:21px;letter-spacing:.3px}
  .front__circle{position:absolute;right:60px;top:40px;width:180px;height:180px;border:5px solid var(--light);border-radius:50%}

  /* back */
  .back__brand{position:absolute;left:40px;top:56px;display:flex;align-items:center;gap:12px}
  .back__brand-dot{width:46px;height:46px;border:2.5px solid var(--ink);border-radius:50%}
  .back__brand-name{font-family:"Cinzel",serif;font-size:23px;color:var(--ink);letter-spacing:.5px}
  .address{position:absolute;left:40px;top:116px;font-family:"Montserrat",sans-serif;font-size:14px;line-height:20px;color:var(--ink)}
  .tagline{position:absolute;left:40px;top:182px;font-family:"Cinzel",serif;font-size:15px;color:var(--accent-ink);letter-spacing:.5px}
  .person{position:absolute;right:36px;top:28px;text-align:right;font-family:"Montserrat",sans-serif;font-size:12.5px;line-height:18px;color:var(--ink)}
  .person__name{font-family:"Cinzel",serif;font-size:17px;color:var(--accent-ink)}
  .wave{position:absolute;inset:0}
  .contacts{position:absolute;right:34px;top:162px;list-style:none;text-align:right;font-family:"Montserrat",sans-serif;font-size:13px;color:var(--paper)}
  .contacts li{display:flex;justify-content:flex-end;align-items:center;gap:8px;line-height:22px}
  .contacts li.gap{margin-top:12px}
  .contacts svg{width:11px;height:11px}
  .motto{position:absolute;left:40px;bottom:18px;font-family:"Cinzel",serif;font-size:15px;letter-spacing:.5px;color:var(--paper)}
</style>
</head>
<body>
<main class="canvas">

  <section class="card card--front">
    <div class="front__brand">Tallowmere Wealth</div>
    <ul class="services">
      <li>Life &amp; TPD Insurance</li>
      <li>Income Protection</li>
      <li>Financial Planning</li>
      <li>Retirement Planning</li>
    </ul>
    <p class="licensee">Northgate Advisory Limited<br>Australian Financial Services Licensee-License Number 418203</p>
    <div class="front__circle"></div>
  </section>

  <section class="card card--back">
    <svg class="wave" viewBox="0 0 600 365" preserveAspectRatio="none">
      <path d="M0,264 C150,264 255,236 322,182 C400,118 515,96 600,92 L600,365 L0,365Z" fill="var(--mid-grey)"/>
      <path d="M0,282 C150,282 258,252 326,198 C405,134 518,112 600,108 L600,365 L0,365Z" fill="var(--paper)"/>
      <path d="M0,300 C150,300 260,270 330,215 C410,150 520,128 600,124 L600,365 L0,365Z" fill="var(--charcoal)"/>
    </svg>

    <div class="person">
      <div><span class="person__name">Sam Hale</span> | B.Ag.Ec. Dip F.P. CFP®</div>
      <div>Managing Director</div>
      <div>Authorised Representative</div>
    </div>

    <div class="back__brand">
      <span class="back__brand-dot"></span>
      <span class="back__brand-name">Tallowmere Wealth</span>
    </div>
    <p class="address">Suite 4A, 18 Colvin St<br>Riverbend, QLD 4170<br>PO Box 5312, Westhaven</p>
    <p class="tagline">‘Financial Peace of Mind’</p>

    <ul class="contacts">
      <li>0400 512 388
        <svg viewBox="0 0 12 12"><rect x="3" y="1" width="6" height="10" rx="1" fill="none" stroke="#fff"/></svg></li>
      <li>(07) 3000 1274
        <svg viewBox="0 0 12 12"><path d="M2,3 Q6,0 10,3 L9,5 L7,4 L5,4 L3,5Z M3,7 H9 V10 H3Z" fill="#fff"/></svg></li>
      <li>(07) 3000 1275
        <svg viewBox="0 0 12 12"><rect x="2" y="4" width="8" height="6" fill="#fff"/><rect x="3.5" y="1" width="5" height="3" fill="none" stroke="#fff"/></svg></li>
      <li class="gap">sam@tallowmerewealth.com.au
        <svg viewBox="0 0 12 12"><rect x="1" y="3" width="10" height="7" fill="none" stroke="#fff"/><path d="M1,3 L6,7 L11,3" fill="none" stroke="#fff"/></svg></li>
      <li>www.tallowmerewealth.com.au
        <svg viewBox="0 0 12 12"><circle cx="6" cy="6" r="5" fill="none" stroke="#fff"/><path d="M1,6 H11 M6,1 V11" stroke="#fff"/></svg></li>
    </ul>

    <p class="motto">A Referral Built Business</p>
  </section>

</main>
</body>
</html>
```